The Visual Personality of Miss Cobbler Food Trailer

Something that stands out with color and our logo. This is a food trailer that attends several events in the spring and summer. We are known for being one of the best Gumbo producers in mid Michigan. We have been responsible for connecting different communities and cultures together and we are strong supporters of our veterans since this is a veteran owned business. All of our vegetables are fresh and locally purchased. These recipes are originally from New Orleans Louisiana. Our website is Misscobbler.net. This will be used for an 8" x 11" poster. Leave a box or area that states "WHERE WE WILL BE:" so that we can add the location of the event that we are attending.

Target Market(s)

We do cuisine that is recognized in the southern states of the USA. but live in the northern part of the USA. We are providing a menu of different southern recipes so they do not have to go all the way down south for get..

Industry/Entity Type

Food/Restaurant Industry

Font styles to use
Serif
Decorative

Colors
0094D4
00A9DD
6FCCEA
C7EBF8
E9F6FB
59FF00
82FF00
B8FF75
E3FFCB
F4FFEA
FFF300
FFF600
FEFA6F
FFFEC7
FFFEE8
EE7325
F08F49
F5BC92
FAE3D3
FDF4ED
EB3D1F
EC4F4E
F09395
F8D3D4
FCEDEE
A7469A
B969AE
D3A5CF
EDDBEB
F8F0F9

Requirements
Must have
• Our logo, which is "Miss Cobbler", "Homemade Deliciousness". We need an area on the poster where we can manually add the location of the event we will be attending because it changes weekly. location
Nice to have
• Bold colors and logo

```html
<!DOCTYPE html>
<html lang="en">
<head>
<meta charset="utf-8">
<title>Miss Cobbler Food Trailer – Poster</title>
<link rel="stylesheet" href="https://fonts.googleapis.com/css2?family=Bree+Serif&family=Abhaya+Libre:wght@800&family=Dancing+Script:wght@500&display=swap">
<style>
  :root {
    --white: #ffffff;
    --cream: #fffee8;
    --strip: #fdf4ed;
    --ink: #1c1c1c;
    --gold: #fef06f;
    --orange: #f08f49;
    --orange-deep: #ee7325;
    --red: #eb3d1f;
    --red-bold: #e3061b;
    --pink-soft: #f5c6bf;
    --bread: #d9924f;
    --tomato: #d8362a;
    --lettuce: #cfe0b0;
    --stew: #c8502c;
  }
  * { margin: 0; padding: 0; box-sizing: border-box; }
  html, body { width: 848px; height: 1200px; overflow: hidden; background: var(--white); }
  .poster { position: relative; width: 848px; height: 1200px; overflow: hidden; background: var(--strip); }

  .hero-photo {
    position: absolute; left: 0; top: 0; width: 848px; height: 572px;
    background:
      radial-gradient(ellipse 30% 22% at 62% 45%, var(--tomato), transparent 70%),
      radial-gradient(ellipse 25% 18% at 32% 78%, var(--tomato), transparent 70%),
      radial-gradient(ellipse 45% 20% at 60% 70%, var(--lettuce), transparent 75%),
      linear-gradient(160deg, #efe3d2 0%, var(--bread) 35%, #c97b3c 60%, #e8d7c4 100%);
  }

  .brand-badge {
    position: absolute; left: 0; top: -16px; width: 286px; height: 286px;
    border-radius: 50%; background: var(--white);
    display: flex; flex-direction: column; align-items: center; justify-content: center;
    transform: translate(0, 0);
  }
  .brand-name {
    font-family: "Bree Serif", Georgia, serif; font-size: 40px; line-height: 1.05;
    color: var(--ink); text-align: center; letter-spacing: 1px;
  }
  .brand-tagline {
    margin-top: 10px;
    font-family: "Bree Serif", Georgia, serif; font-size: 11px; letter-spacing: 1px;
    color: var(--ink); text-transform: uppercase;
  }

  .promo {
    position: absolute; left: 0; top: 589px; width: 848px; height: 611px;
    background: linear-gradient(90deg, var(--orange) 0%, #f47548 50%, var(--red) 100%);
  }

  .headline {
    position: absolute; left: 18px; width: 420px; top: 28px; text-align: center;
    font-family: "Dancing Script", cursive; font-size: 52px; line-height: 1.25;
    color: var(--gold);
  }
  .lead {
    position: absolute; left: 18px; width: 420px; top: 196px; text-align: center;
    font-family: "Abhaya Libre", Georgia, serif; font-weight: 800; font-size: 30px;
    line-height: 1.05; letter-spacing: 2px; color: var(--white);
  }

  .snapshot {
    position: absolute; background: var(--cream); padding: 9px;
    box-shadow: 0 3px 8px rgba(0,0,0,.25);
  }
  .snapshot-fill { width: 100%; height: 100%; }
  .snapshot--gumbo { left: 470px; top: 16px; width: 330px; height: 236px; transform: rotate(4deg); }
  .snapshot--gumbo .snapshot-fill {
    background: radial-gradient(ellipse 55% 60% at 45% 45%, var(--stew), #9a3a1f 70%, #e9e4dd 100%);
  }
  .snapshot--sandwich { left: 515px; top: 292px; width: 232px; height: 176px; transform: rotate(-4deg); }
  .snapshot--sandwich .snapshot-fill {
    background: linear-gradient(170deg, #d99a52 0%, #b9733a 40%, #6f7a3a 60%, #caa477 100%);
  }

  .location-panel {
    position: absolute; left: 0; top: 360px; width: 418px; height: 251px;
    background: var(--red-bold); border-top-right-radius: 22px;
  }
  .location-title {
    position: absolute; left: 29px; top: 22px;
    font-family: "Bree Serif", Georgia, serif; font-size: 31px; color: var(--white);
  }
  .location-box {
    position: absolute; left: 28px; top: 81px; width: 366px; height: 137px;
    background: var(--cream);
    display: flex; align-items: center; justify-content: center;
  }
  .location-placeholder {
    font-family: "Abhaya Libre", Georgia, serif; font-weight: 800; font-size: 20px;
    letter-spacing: 3px; color: var(--pink-soft);
  }

  .website {
    position: absolute; left: 520px; width: 230px; top: 534px; text-align: center;
    font-family: "Bree Serif", Georgia, serif; font-size: 24px; color: var(--white);
  }
</style>
</head>
<body>
  <main class="poster">
    <div class="hero-photo" role="img" aria-label="Photo of a fried po'boy sandwich with tomato, shredded lettuce and remoulade on French bread"></div>

    <div class="brand-badge">
      <span class="brand-name">Miss<br>Cobbler</span>
      <span class="brand-tagline">Homemade Deliciousness!</span>
    </div>

    <section class="promo">
      <h1 class="headline">Homemade<br>Deliciousness</h1>
      <p class="lead">created from fresh<br>and authentic<br>ingredients</p>

      <figure class="snapshot snapshot--gumbo">
        <div class="snapshot-fill" role="img" aria-label="Photo of a bowl of gumbo with tomatoes and green peppers"></div>
      </figure>
      <figure class="snapshot snapshot--sandwich">
        <div class="snapshot-fill" role="img" aria-label="Photo of a stacked sandwich with greens and tomato"></div>
      </figure>

      <div class="location-panel">
        <h2 class="location-title">where we will be</h2>
        <div class="location-box">
          <span class="location-placeholder">YOUR ADDRESS HERE</span>
        </div>
      </div>

      <p class="website">www.misscobbler.net</p>
    </section>
  </main>
</body>
</html>
```